need corporate, modern business card created for Consulting Company

I need a slick business card using elements from my website, as well as, integrating my pixelforge-created logo (see files).

The business card needs to be:
1. Corporate and modern
2. Clean and professional

I've included a PSD with the logo/icon that you can use to create it. Feel free to try a metallic finish on the logo, make it bigger/small, underlay it. Whatever you need to do to make my card stand out.

Try a black background, or white background or gray.

The idea is for my card to be memorable as well as professional and corporate.

Target Market(s)

Corporate business in the US and Canada.

Industry/Entity Type

Business

Contact Information for Business Card

Commerce Advancing Methods
Martin Coles, Senior Partner
office: 1 877 555 0143
mobile: 1 519 555 0172
website: http://www.brightvale.example

Requirements
Must have
• Card-related information
• corporate, yet modern
• clean and professional
• incorporate the icon only
• must have an editable form when complete!
Nice to have
• metallic icon might be cool
• try it with white or black

```html
<!DOCTYPE html>
<html lang="en">
<head>
<meta charset="utf-8">
<title>Brightvale Business Card</title>
<link href="https://fonts.googleapis.com/css2?family=Nunito+Sans:wght@400;600;700&display=swap" rel="stylesheet">
<style>
  :root {
    --backdrop: #e6e3df;
    --card-light: #ffffff;
    --card-dark: #232323;
    --brand-blue: #3a6db4;
    --ink: #1d1d1d;
    --ink-soft: #2b2b2b;
    --divider: #555555;
    --emboss: #161616;
  }
  * { box-sizing: border-box; margin: 0; padding: 0; }
  html, body {
    width: 1200px;
    height: 1000px;
    overflow: hidden;
    background: var(--backdrop);
    font-family: "Nunito Sans", Arial, sans-serif;
  }
  .canvas {
    position: relative;
    width: 1200px;
    height: 1000px;
  }
  .card {
    position: absolute;
    left: 265px;
    width: 665px;
    height: 397px;
    box-shadow: 0 4px 10px rgba(0,0,0,0.25);
  }
  .card--front { top: 73px; background: var(--card-light); }
  .card--back { top: 532px; background: var(--card-dark); }

  .brand-name {
    position: absolute;
    font-weight: 700;
    letter-spacing: -0.5px;
    line-height: 1;
  }
  .card--front .brand-name {
    left: 40px;
    top: 186px;
    font-size: 44px;
    color: var(--brand-blue);
  }
  .card--back .brand-name {
    left: 0;
    right: 0;
    top: 168px;
    text-align: center;
    font-size: 62px;
    color: var(--emboss);
  }

  .divider {
    position: absolute;
    left: 325px;
    top: 99px;
    width: 1px;
    height: 200px;
    background: var(--divider);
  }
  .details {
    position: absolute;
    left: 353px;
    top: 112px;
    color: var(--ink-soft);
  }
  .person-name {
    font-size: 21px;
    font-weight: 700;
    color: var(--ink);
    line-height: 1.1;
  }
  .person-title {
    font-size: 17px;
    line-height: 1.3;
  }
  .contact-list {
    list-style: none;
    margin-top: 19px;
  }
  .contact-list li {
    display: flex;
    align-items: center;
    gap: 6px;
    font-size: 17px;
    line-height: 22px;
  }
  .contact-list svg {
    width: 14px;
    height: 14px;
    fill: var(--brand-blue);
  }
  .tagline {
    margin-top: 16px;
    font-size: 17px;
  }
</style>
</head>
<body>
<main class="canvas">
  <section class="card card--front" aria-label="Card front">
    <div class="brand-name">brightvale</div>
    <div class="divider"></div>
    <div class="details">
      <p class="person-name">Martin Coles</p>
      <p class="person-title">Senior Partner</p>
      <ul class="contact-list">
        <li>
          <svg viewBox="0 0 16 16" aria-hidden="true"><path d="M4 1l3 3-2 2c1 2 3 4 5 5l2-2 3 3-2 3C7 15 1 9 1 3z"/></svg>
          1 519 555 0172
        </li>
        <li>
          <svg viewBox="0 0 16 16" aria-hidden="true"><path d="M1 5c0-2 3-3 7-3s7 1 7 3v2h-4V5H5v2H1z"/><rect x="3" y="8" width="10" height="6" rx="1"/></svg>
          1 877 555 0143
        </li>
        <li>
          <svg viewBox="0 0 16 16" aria-hidden="true"><path d="M8 1a7 7 0 100 14A7 7 0 008 1zm0 1.5c.8 0 1.7 1.6 2 4H6c.3-2.4 1.2-4 2-4zM2.6 6.5h2.3a12 12 0 000 3H2.6a5.5 5.5 0 010-3zm3.4 0h4a11 11 0 010 3H6a11 11 0 010-3zm5.1 0h2.3a5.5 5.5 0 010 3h-2.3a12 12 0 000-3zM6 10.5h4c-.3 2.4-1.2 4-2 4s-1.7-1.6-2-4z"/></svg>
          www.brightvale.example
        </li>
      </ul>
      <p class="tagline">Commerce Advancing Methods</p>
    </div>
  </section>

  <section class="card card--back" aria-label="Card back">
    <div class="brand-name">brightvale</div>
  </section>
</main>
</body>
</html>
```